Halverstone Minerals Web Design

Require a Web page design for an international mining and private investment company currently based in Dubai, UAE. I would like to view designs that incorporate our current corporate logo design aimed at communicating global business development/expansion across a diversity of commodities within the mining and investment sectors.

We are a global organisation with global experience and strategy with specific business development focus in Africa, Central and South America.

Target Market(s)

Mining industry, finance, fund raising, brokering, private equity and public stock exchanges.

Industry/Entity Type

Mining

Number of Pages Required

5+ page

Font styles to use
Sans Serif

Colors

Designer to choose colors to be used in the design.

Requirements
Must have
• Corporate logo, description of who we are, what we do, corporate mission, vision & strategy.
Nice to have
• Inclusion of images, photos, interactive maps/graphics and video.

```html
<!DOCTYPE html>
<html lang="en">
<head>
<meta charset="utf-8">
<title>Halverstone Minerals</title>
<link href="https://fonts.googleapis.com/css2?family=Lato:wght@400;700;900&display=swap" rel="stylesheet">
<style>
:root{
  --gold:#c4a55e;
  --gold-dark:#a98b45;
  --ink:#2b2b2b;
  --text:#444;
  --muted:#666;
  --light:#efefef;
  --white:#fff;
  --footer:#262626;
  --footer-text:#cfcfcf;
}
*{box-sizing:border-box;margin:0;padding:0}
html,body{width:1200px;height:3041px;overflow:hidden}
body{font-family:"Lato",Arial,sans-serif;color:var(--text);background:var(--white);position:relative}
.abs{position:absolute}
a{color:inherit;text-decoration:none}

/* header */
.site-header{position:absolute;left:0;top:0;width:1200px;height:162px;background:var(--white)}
.header-line{position:absolute;left:0;top:0}
.contact-strip{position:absolute;right:48px;top:20px;display:flex;gap:36px;font-size:14px;color:var(--ink);font-weight:700;align-items:center}
.contact-strip span{display:flex;align-items:center;gap:14px}
.brand{position:absolute;left:75px;top:62px;display:flex;align-items:center;gap:12px}
.brand-mark{width:44px;height:44px;background:var(--gold)}
.brand-name{font-size:26px;font-weight:700;color:var(--gold);letter-spacing:.5px}
.main-nav{position:absolute;right:75px;top:106px;display:flex;gap:38px;font-size:12.5px;font-weight:700;color:var(--ink);letter-spacing:.2px}
.main-nav .active{color:var(--gold)}

/* hero */
.hero{position:absolute;left:0;top:162px;width:1200px;height:501px;overflow:hidden}
.hero-photo{position:absolute;inset:0;
  background:
    radial-gradient(ellipse 420px 380px at 600px 300px,rgba(120,88,62,.55),rgba(120,88,62,0) 70%),
    linear-gradient(180deg,#8b9096 0%,#747980 45%,#5b5f65 100%)}
.hero-title{position:absolute;left:0;width:1200px;top:178px;text-align:center;color:var(--white);font-size:56px;font-weight:900;letter-spacing:.5px}
.hero-sub{position:absolute;left:0;width:1200px;top:250px;text-align:center;color:var(--white);font-size:20px;font-weight:700}
.hero-dots{position:absolute;left:562px;top:466px;display:flex;gap:8px}
.hero-dots i{width:13px;height:13px;border-radius:50%;background:var(--white);display:block}
.hero-dots i.on{background:var(--gold)}

/* section headings */
.section-title{font-size:30px;font-weight:900;color:var(--ink);letter-spacing:.5px}
.section-title em{font-style:normal;color:var(--gold)}
.btn-dark{display:inline-block;background:var(--ink);color:var(--white);font-size:13px;font-weight:700;border-radius:24px;width:165px;height:44px;line-height:44px;text-align:center;letter-spacing:.3px}

/* who */
.who{position:absolute;left:0;top:663px;width:1200px;height:371px;text-align:center}
.who .section-title{position:absolute;left:0;width:1200px;top:70px}
.who-text{position:absolute;left:78px;width:1044px;top:126px;font-size:14px;line-height:23px;color:var(--text)}
.who .btn-dark{position:absolute;left:518px;top:269px}

/* what */
.what{position:absolute;left:0;top:1034px;width:1200px;height:432px;background:var(--light)}
.service-card{position:absolute;top:65px;width:242px;height:306px;background:var(--white);text-align:center}
.service-card svg{margin-top:30px}
.service-card h3{font-size:20px;font-weight:900;color:var(--ink);margin-top:22px}
.service-card h3 em{font-style:normal;color:var(--gold)}
.service-card p{font-size:14px;line-height:23px;color:var(--text);margin:8px 28px 0}
.service-card .more{position:absolute;left:0;width:100%;bottom:30px;font-size:12px;color:var(--gold);text-decoration:underline;letter-spacing:.3px}
.what-body{position:absolute;left:622px;top:58px;width:505px}
.what-body p{font-size:14.5px;line-height:23px;margin-top:10px;color:var(--text)}
.what-body .section-title{margin-bottom:14px}
.what .btn-dark{position:absolute;left:622px;top:326px}

/* mission / vision */
.pillars{position:absolute;left:0;top:1466px;width:1200px;height:332px}
.pillar-label{position:absolute;color:var(--white);font-size:23px;font-weight:700;text-align:center;width:340px}

/* banner */
.banner{position:absolute;left:0;top:1800px;width:1200px;height:426px;
  background:linear-gradient(180deg,#5d6e82 0%,#4c5766 40%,#3a3a3c 75%,#2d2a27 100%)}
.banner-text{position:absolute;left:0;width:1200px;top:168px;text-align:center;color:var(--white);font-size:29px;font-weight:700;line-height:43px;letter-spacing:.5px}

/* blog */
.blog{position:absolute;left:0;top:2226px;width:1200px;height:511px}
.blog .section-title{position:absolute;left:0;width:1200px;top:51px;text-align:center}
.post{position:absolute;top:119px;width:331px}
.post-image{width:331px;height:193px}
.post h4{font-size:19px;font-weight:700;color:var(--ink);margin-top:20px}
.post p{font-size:14px;line-height:22px;color:var(--text);margin-top:10px}
.post .more{display:block;margin-top:12px;font-size:14px;color:var(--gold)}

/* footer */
.site-footer{position:absolute;left:0;top:2737px;width:1200px;height:304px;background:var(--footer);border-top:5px solid var(--gold);color:var(--footer-text);font-size:12.5px}
.footer-brand{position:absolute;left:75px;top:108px;display:flex;align-items:center;gap:10px}
.footer-brand .brand-mark{width:36px;height:36px}
.footer-brand .brand-name{font-size:21px}
.copyright{position:absolute;left:75px;top:168px;line-height:21px;color:#e6e6e6}
.footer-col{position:absolute;top:58px}
.footer-col h5{font-size:13.5px;font-weight:700;color:var(--gold);letter-spacing:.4px;margin-bottom:14px}
.footer-col li{list-style:none;line-height:27.5px}
.footer-col .strong{color:var(--white);font-weight:700}
.footer-col .row{display:flex;align-items:center;gap:10px}
.social{display:flex;gap:14px;margin-top:4px}
.social i{width:16px;height:16px;border-radius:50%;background:var(--white);display:block}
.footer-follow h5{color:var(--white)}
</style>
</head>
<body>

<header class="site-header">
  <svg class="header-line" width="1200" height="62" viewBox="0 0 1200 62">
    <polyline points="0,2 676,2 742,58 1200,58" fill="none" stroke="var(--gold)" stroke-width="3"/>
  </svg>
  <div class="contact-strip">
    <span>
      <svg width="13" height="13" viewBox="0 0 24 24"><path d="M6.6 10.8a15 15 0 006.6 6.6l2.2-2.2a1 1 0 011-.25 11.4 11.4 0 003.6.6 1 1 0 011 1V20a1 1 0 01-1 1A17 17 0 013 4a1 1 0 011-1h3.5a1 1 0 011 1c0 1.25.2 2.45.6 3.6a1 1 0 01-.25 1z" fill="var(--gold)"/></svg>
      1-800-555-0142
    </span>
    <span>
      <svg width="14" height="11" viewBox="0 0 24 18"><rect width="24" height="18" rx="2" fill="var(--gold)"/><path d="M1 2l11 8 11-8" fill="none" stroke="#fff" stroke-width="2"/></svg>
      info@halverstone.example
    </span>
  </div>
  <div class="brand">
    <span class="brand-mark"></span>
    <span class="brand-name">Halverstone Minerals</span>
  </div>
  <nav class="main-nav">
    <a class="active">HOME</a><a>WHO WE ARE</a><a>WHAT WE DO</a><a>CORPORATE MISSION</a><a>VISION &amp; STRATEGY</a><a>CONTACT</a>
  </nav>
</header>

<section class="hero">
  <div class="hero-photo" role="img" aria-label="Businessman drawing a rising chart over a city skyline"></div>
  <h1 class="hero-title">HALVERSTONE MINERALS</h1>
  <p class="hero-sub">Phasellus vel massa quis orci venenatis laoreet malesuada facilisis</p>
  <div class="hero-dots"><i class="on"></i><i></i><i></i><i></i></div>
</section>

<section class="who">
  <h2 class="section-title"><em>WHO</em> WE ARE</h2>
  <p class="who-text">Sed vulputate mollis ipsum, tempor tincidunt mauris cursus eget. Nunc dui turpis, faucibus nec ligula et, efficitur bibendum felis. Vivamus fringilla arcu et diam malesuada, ut elementum tortor pulvinar. Vivamus vitae dolor auctor, iaculis leo non, efficitur erat. Donec pharetra turpis ut arcu aliquet, eget convallis ipsum pretium. Nunc eget arcu ut erat tempus hendrerit quis nec turpis. Praesent posuere enim libero.<br>Ut vulputate lorem lorem, sit amet pulvinar dolor commodo sit amet. Nullam tincidunt eros ligula, a iaculis libero semper sed. Phasellus ex ante, iaculis sed arcu et, lobortis blandit mi. Phasellus at dolor eget ipsum ullamcorper sagittis vel vel metus.</p>
  <a class="btn-dark">READ MORE</a>
</section>

<section class="what">
  <article class="service-card" style="left:75px">
    <svg width="62" height="62" viewBox="0 0 62 62"><path d="M6 56h50L36 28 26 40 20 34z" fill="var(--ink)"/><path d="M14 10l22 22" stroke="var(--ink)" stroke-width="4"/><path d="M8 18q10-14 24-12" fill="none" stroke="var(--ink)" stroke-width="4"/></svg>
    <h3><em>Mining</em> Company</h3>
    <p>Sed vulputate mollis ipsum, tempor tincidunt mauris cursus eget amet pulvinar dolor commodo..</p>
    <a class="more">MORE INFO</a>
  </article>
  <article class="service-card" style="left:347px">
    <svg width="62" height="62" viewBox="0 0 62 62"><rect x="8" y="36" width="9" height="20" fill="var(--ink)"/><rect x="21" y="28" width="9" height="28" fill="var(--ink)"/><rect x="34" y="20" width="9" height="36" fill="var(--ink)"/><rect x="47" y="12" width="9" height="44" fill="var(--ink)"/><path d="M8 26l14-10 10 6 20-14" fill="none" stroke="var(--ink)" stroke-width="3"/></svg>
    <h3><em>Private</em> Investment</h3>
    <p>Effective contract management delivered through our Contract Advisory ensures</p>
    <a class="more">MORE INFO</a>
  </article>
  <div class="what-body">
    <h2 class="section-title"><em>WHAT</em> WE DO</h2>
    <p>Sed vulputate mollis ipsum, tempor tincidunt mauris cursus eget.<br>Nunc dui turpis, faucibus nec ligula et, efficitur bibendum felis. Vivamus fringilla arcu et diam malesuada, ut elementum tortor pulvinar. Vivamus vitae dolor auctor, iaculis leo non, efficitur erat. Donec pharetra turpis ut arcu aliquet, eget convallis ipsum pretium. Nunc eget arcu ut erat tempus hendrerit quis nec turpis.</p>
    <p>Nunc eget arcu ut erat tempus hendrerit quis nec turpis. Praesent posuere enim libero.</p>
  </div>
  <a class="btn-dark">READ MORE</a>
</section>

<section class="pillars">
  <svg class="abs" style="left:0;top:0" width="1200" height="332" viewBox="0 0 1200 332">
    <defs>
      <linearGradient id="missionTone" x1="0" y1="0" x2="1" y2="1"><stop offset="0" stop-color="#6b5532"/><stop offset="1" stop-color="#3a2e1c"/></linearGradient>
      <linearGradient id="visionTone" x1="0" y1="0" x2="1" y2="1"><stop offset="0" stop-color="#2a2622"/><stop offset="1" stop-color="#15120f"/></linearGradient>
    </defs>
    <polygon points="0,0 614,0 580,332 0,332" fill="url(#missionTone)" role="img" aria-label="Hands holding a coffee cup beside a tablet showing charts"/>
    <polygon points="618,0 1200,0 1200,332 584,332" fill="url(#visionTone)" role="img" aria-label="Hand placing golden eggs in a nest"/>
    <line x1="616" y1="0" x2="582" y2="332" stroke="#fff" stroke-width="4"/>
    <g transform="translate(262,120)" fill="#fff">
      <path d="M30 0c10 8 14 20 12 34l-8 10H24l-8-10C14 20 20 8 30 0z"/>
      <path d="M16 30l-10 14 12-2zM44 30l10 14-12-2z"/>
      <path d="M24 48l6 12 6-12z"/>
    </g>
    <g transform="translate(870,158)">
      <path d="M0 20Q34-12 68 20Q34 52 0 20z" fill="#fff"/>
      <circle cx="34" cy="20" r="11" fill="#1d1a17"/>
      <circle cx="34" cy="20" r="5" fill="#fff"/>
    </g>
  </svg>
  <div class="pillar-label" style="left:174px;top:198px">Corporate Mission</div>
  <div class="pillar-label" style="left:734px;top:198px">Vision &amp; Strategy</div>
</section>

<section class="banner" role="img" aria-label="Aerial view of a modern city skyline with highways">
  <p class="banner-text">MAECENAS TINCIDUNT LIGULA DIAM, SED MAXIMUS<br>JUSTO FAUCIBUS EU</p>
</section>

<section class="blog">
  <h2 class="section-title"><em>BLOG</em> POSTS</h2>
  <article class="post" style="left:75px">
    <div class="post-image" role="img" aria-label="Business people reviewing documents and a laptop" style="background:linear-gradient(135deg,#c9ccd0,#7d8288)"></div>
    <h4>Phasellus ex ante, iaculis sed arcu</h4>
    <p>Sed vulputate mollis ipsum, tempor tincidunt mauris cursus eget. dui turpis, faucibus nec ligula et, efficitur bibendum felis</p>
    <a class="more">Read More</a>
  </article>
  <article class="post" style="left:435px">
    <div class="post-image" role="img" aria-label="Mine engineers in safety vests beside a haul truck" style="background:linear-gradient(135deg,#c9a25a,#7a5a32)"></div>
    <h4>Phasellus ex ante, iaculis sed arcu</h4>
    <p>Sed vulputate mollis ipsum, tempor tincidunt mauris cursus eget. dui turpis, faucibus nec ligula et, efficitur bibendum felis</p>
    <a class="more">Read More</a>
  </article>
  <article class="post" style="left:795px">
    <div class="post-image" role="img" aria-label="Glowing stock market chart on a dark screen" style="background:linear-gradient(135deg,#1d3a3a,#0e1a22)"></div>
    <h4>Phasellus ex ante, iaculis sed arcu</h4>
    <p>Sed vulputate mollis ipsum, tempor tincidunt mauris cursus eget. dui turpis, faucibus nec ligula et, efficitur bibendum felis</p>
    <a class="more">Read More</a>
  </article>
</section>

<footer class="site-footer">
  <div class="footer-brand">
    <span class="brand-mark"></span>
    <span class="brand-name">Halverstone Minerals</span>
  </div>
  <p class="copyright">Copyright © 2018. Halverstone Minerals.<br>All Right Reserved</p>

  <div class="footer-col" style="left:397px">
    <h5>SITE MAP</h5>
    <ul><li>Home</li><li>Who We Are</li><li>What We Do</li><li>Corporate Mission</li><li>Vision &amp; Strategy</li><li>Contact Us</li></ul>
  </div>

  <div class="footer-col" style="left:614px">
    <h5>CONTACT ADDRESS</h5>
    <ul>
      <li class="strong">Halverstone Minerals</li>
      <li style="line-height:21px;margin-bottom:4px">42 Quarry Lane<br>Dunmore, QL7 3RB</li>
      <li class="row"><svg width="11" height="11" viewBox="0 0 24 24"><path d="M6.6 10.8a15 15 0 006.6 6.6l2.2-2.2a1 1 0 011-.25 11.4 11.4 0 003.6.6 1 1 0 011 1V20a1 1 0 01-1 1A17 17 0 013 4a1 1 0 011-1h3.5a1 1 0 011 1c0 1.25.2 2.45.6 3.6a1 1 0 01-.25 1z" fill="#fff"/></svg>1-800-555-0142</li>
      <li class="row"><svg width="12" height="9" viewBox="0 0 24 18"><rect width="24" height="18" rx="2" fill="#fff"/><path d="M1 2l11 8 11-8" fill="none" stroke="#262626" stroke-width="2"/></svg>info@halverstone.example</li>
      <li class="row"><svg width="10" height="13" viewBox="0 0 20 26"><path d="M10 0a9 9 0 019 9c0 7-9 17-9 17S1 16 1 9a9 9 0 019-9z" fill="#fff"/><circle cx="10" cy="9" r="3.5" fill="#262626"/></svg>Map Direction</li>
    </ul>
  </div>

  <div class="footer-col footer-follow" style="left:894px">
    <h5>FOLLOW US</h5>
    <div class="social"><i></i><i></i><i></i><i></i><i></i><i></i></div>
  </div>
</footer>

</body>
</html>
```